Flyer für Verkauf von Radondetektoren
Zielgruppe
Ich verkaufe Radondetektoren zur Messung von Radon in Innenräumen. Zielgruppe sind Privatpersonen, Firmen, Genossenschaften und andere Hauseigentümer.
Aufgabenstellung
Ich brauche das Design für meine Messanleitung.
Kreativ - modern - weniger kann mehr sein
Struktur ist wichtigt, es soll also einfach sein zu lesen und zu verstehen, was gemacht werden soll. Können Bulletpoints, Icons mit eingebracht werden.
Wichtig ist auch, dass die beiden Logos 'Luftprüfer.de' und TESTOVAL' auf der Messanleitung vorhanden sind. Wobei 'Luftprüfer.de' das Hauptlogo ist.
DIN format dachte ich A4 beidseitig (Text müsste also auf diese Grösse angepasst werden).
Kann natürlich auch Flyer-Format sein oder andere Vorschläge!
Bildmaterial gibt es auf unsere Homepage https://luftprüfer.de und https://luftkontroll.se . Diese haben wir bereits gekauft und können verwendet werden. Ich lade sie den bei Bedarf hoch. Es können natürlich auch andere Vorschläge kommen.

```html
<!DOCTYPE html>
<html lang="de">
<head>
<meta charset="utf-8">
<title>Messanleitung Radondetektoren</title>
<link href="https://fonts.googleapis.com/css2?family=Barlow:ital,wght@0,400;0,500;0,700;0,800;1,400;1,700;1,800&display=swap" rel="stylesheet">
<style>
:root{
  --red:#e30613;
  --ink:#444446;
  --band-a:#f2f2f2;
  --white:#ffffff;
}
*{margin:0;padding:0;box-sizing:border-box}
html,body{width:1200px;height:848px;overflow:hidden;background:var(--white)}
.sheet{position:relative;width:1200px;height:848px;font-family:"Barlow",Arial,sans-serif;color:var(--ink);overflow:hidden}
.block{position:absolute}
.body-text{font-size:13.8px;line-height:18.5px}
.ln{display:block;white-space:nowrap;text-align:justify;text-align-last:justify}
.ln.end{text-align-last:left}
.ln.tight{letter-spacing:-0.35px;word-spacing:-1px}
.note{font-style:italic;margin-top:18.5px}
.bullet::before{content:"»";font-weight:500;font-size:20px;line-height:17px;color:var(--ink);margin-right:9px;vertical-align:-1px}

/* step bands */
.step-band{position:absolute;left:0;width:330px;height:60px;
  background:repeating-linear-gradient(135deg,var(--band-a) 0 3px,#dcdcdc 3px 5px);
  background-color:var(--band-a)}
.step-band::after{content:"";position:absolute;inset:0;background:linear-gradient(90deg,rgba(255,255,255,.55),rgba(255,255,255,0) 70%)}
.step-label{position:absolute;left:24px;z-index:1;font-size:19px;letter-spacing:.5px;color:var(--ink)}
.step-label b{font-size:34px;font-weight:800;margin-right:6px;vertical-align:-3px}
.step-badge{position:absolute;left:313px;width:64px;height:64px;border-radius:50%;background:var(--red);border:3px solid var(--white);z-index:2;display:flex;align-items:center;justify-content:center}

.section-title{font-size:27.5px;line-height:33px;font-weight:800;letter-spacing:.6px;color:var(--ink)}
.sub-title{position:absolute;color:var(--red);font-weight:700;font-size:16.8px;line-height:18.8px}

.url-button{position:absolute;left:36px;top:249px;width:332px;height:38px;border-radius:19px;background:var(--red);color:var(--white);font-weight:700;font-size:16.5px;padding:9px 0 0 18px;letter-spacing:.2px}

.intro{position:absolute;left:481px;top:36px;font-weight:700;font-style:italic;font-size:16px;line-height:21.5px;color:var(--ink)}

.contact-bar{position:absolute;left:404px;top:760px;width:796px;height:88px;background:var(--red);border-top-left-radius:14px;color:var(--white)}
.contact-text{position:absolute;left:106px;top:18px;font-style:italic;font-weight:700;font-size:16.3px;line-height:21.5px}
.contact-text span{font-weight:400}
</style>
</head>
<body>
<div class="sheet">

  <!-- Step 1 -->
  <div class="step-band" style="top:29px"></div>
  <div class="step-label" style="top:40px"><b>1.</b>SCHRITT</div>
  <div class="step-badge" style="top:26px">
    <svg width="36" height="42" viewBox="0 0 36 42" aria-hidden="true">
      <circle cx="15" cy="9" r="6" fill="#fff"/>
      <path d="M4 26c0-7 5-10 11-10 4 0 7 1 9 3v7z" fill="#fff"/>
      <rect x="20" y="19" width="10" height="8" rx="1.5" fill="#fff"/>
      <path d="M22 19v-2a3 3 0 0 1 6 0v2" stroke="#fff" stroke-width="1.6" fill="none"/>
      <text x="18" y="39" text-anchor="middle" font-family="Barlow,Arial,sans-serif" font-weight="800" font-size="9" fill="#fff">LOGIN</text>
    </svg>
  </div>

  <h1 class="section-title block" style="left:24px;top:108px">REGISTRIERUNG<br>UND ANMELDUNG</h1>

  <div class="block body-text" style="left:24px;top:191px;width:356px">
    <p><span class="ln">Wenn Sie Neukunde sind, legen Sie bitte zunächst ein</span><span class="ln end">neues Benutzerkonto auf unserem Online-Portal an:</span></p>
  </div>

  <div class="url-button">https://radonkund.testoval.se/de</div>
  <svg class="block" style="left:316px;top:258px" width="38" height="52" viewBox="0 0 38 52" aria-hidden="true">
    <g stroke="#444" stroke-width="1.4" fill="none" stroke-linecap="round">
      <path d="M14 3v4M7 6l3 3M21 6l-3 3M5 13h4M19 13h4"/>
    </g>
    <path d="M12 14a2.5 2.5 0 0 1 5 0v13l1-6a2.4 2.4 0 0 1 4.5 1v6l1-4a2.3 2.3 0 0 1 4.3 1v5l.8-2.5a2.2 2.2 0 0 1 4.2 1.2V37c0 7-5 12-11 12h-3c-5 0-7-3-9-6l-6-9a2.5 2.5 0 0 1 4-3l4 5z" fill="#fff" stroke="#444" stroke-width="1.6" stroke-linejoin="round"/>
  </svg>

  <div class="block body-text" style="left:24px;top:320px;width:356px">
    <p>
      <span class="ln">Anschließend können Sie die Radondetektoren registrieren.</span>
      <span class="ln">Vermerken Sie den Start der Messung (Datum und Uhrzeit),</span>
      <span class="ln">die Messorte (Raum und Etage) sowie die 9-stellige Serien-</span>
      <span class="ln">nummer der Detektoren, die Sie auf der Verpackung oder auf</span>
      <span class="ln end">der Unterseite der jeweiligen Detektoren finden.</span>
    </p>
    <p class="note">
      <span class="ln">Firmenkunden haben die Möglichkeit eine Excel-Datei als</span>
      <span class="ln">Hilfsmittel herunterzuladen, die Sie ausfüllen und dann wie-</span>
      <span class="ln end">der hochladen.</span>
    </p>
  </div>

  <!-- Step 2 -->
  <div class="step-band" style="top:511px"></div>
  <div class="step-label" style="top:522px"><b>2.</b>SCHRITT</div>
  <div class="step-badge" style="top:508px">
    <svg width="30" height="36" viewBox="0 0 30 36" aria-hidden="true">
      <path d="M15 2C8 2 3 7 3 13c0 8 12 21 12 21s12-13 12-21C27 7 22 2 15 2z" fill="#fff"/>
      <circle cx="15" cy="13" r="5" fill="var(--red)"/>
    </svg>
  </div>

  <h1 class="section-title block" style="left:24px;top:590px">PLATZIERUNG<br>DER DETEKTOREN</h1>

  <div class="block body-text" style="left:24px;top:673px;width:356px">
    <p>
      <span class="ln">Bevor Sie die Detektoren der Verpackung entnehmen, über-</span>
      <span class="ln">legen Sie wo genau Sie die Radondetektoren platzieren wol-</span>
      <span class="ln">len. Die Radonmessung beginnt, sobald Sie die radondich-</span>
      <span class="ln">ten Verpackungen öffnen. Beachten Sie bei der Platzierung</span>
      <span class="ln">zunächst die Auswahl der Räume und die Positionierung der</span>
      <span class="ln end">Radondetektoren im Raum.</span>
    </p>
  </div>

  <!-- Middle column -->
  <svg class="block" style="left:428px;top:34px" width="46" height="42" viewBox="0 0 46 42" aria-hidden="true">
    <rect x="2" y="6" width="34" height="33" rx="5" fill="none" stroke="var(--red)" stroke-width="3.5"/>
    <path d="M10 19l9 9L42 3" fill="none" stroke="var(--red)" stroke-width="5" stroke-linecap="round" stroke-linejoin="round"/>
  </svg>
  <div class="intro">Für eine zuverlässige Radonmessung<br>empfehlen wir wie folgt vorzugehen:</div>

  <h1 class="section-title block" style="left:428px;top:108px">AUSWAHL DER RÄUME</h1>

  <svg class="block" style="left:428px;top:154px" width="46" height="36" viewBox="0 0 46 36" aria-hidden="true">
    <path d="M1 17L23 3l22 14" fill="none" stroke="var(--red)" stroke-width="3.5" stroke-linejoin="round"/>
    <path d="M7 16h32v20H28V24h-7v12H7z" fill="var(--red)"/>
    <rect x="11" y="22" width="7" height="5" fill="#fff"/>
  </svg>
  <div class="sub-title" style="left:480px;top:172px">Einfamilienhäuser</div>

  <div class="block body-text" style="left:428px;top:210px;width:356px">
    <p>
      <span class="ln bullet">Es sollten mindestens zwei Wohnräume und pro be-</span>
      <span class="ln">wohnte Etage mindestens ein Wohnraum gemessen werden.</span>
      <span class="ln">Wählen Sie Räume aus, in denen Sie sich oft aufhalten (z.B.</span>
      <span class="ln">das Wohn- und Schlafzimmer). Vermeiden Sie aber Räume,</span>
      <span class="ln">in denen das Fenster mehrere Stunden am Tag oder in der</span>
      <span class="ln end">Nacht geöffnet ist.</span>
    </p>
    <p>
      <span class="ln bullet">Insofern Sie einen Keller haben, empfehlen wir alle</span>
      <span class="ln">Kellerräume zu messen, da hier meist das größte Risiko einer</span>
      <span class="ln end">erhöhten Radonkonzentration erwartet wird.</span>
    </p>
  </div>

  <svg class="block" style="left:428px;top:392px" width="46" height="58" viewBox="0 0 46 58" aria-hidden="true">
    <path d="M1 14L23 2l22 12" fill="none" stroke="var(--red)" stroke-width="3.5" stroke-linejoin="round"/>
    <path d="M6 14h34v44H6z" fill="var(--red)"/>
    <g fill="#fff">
      <rect x="13" y="20" width="8" height="7"/><rect x="25" y="20" width="8" height="7"/>
      <rect x="13" y="31" width="8" height="7"/><rect x="25" y="31" width="8" height="7"/>
      <rect x="13" y="42" width="8" height="7"/><rect x="25" y="42" width="8" height="7"/>
    </g>
  </svg>
  <div class="sub-title" style="left:480px;top:412px">Mehrfamilienhäuser, Wohnungen<br>und Wohnkomplexen</div>

  <div class="block body-text" style="left:428px;top:469px;width:356px">
    <p>
      <span class="ln bullet">Alle Wohnungen mit direktem Bodenkontakt sowie min-</span>
      <span class="ln">destens eine Wohnung pro Etage sollten gemessen werden.</span>
      <span class="ln">Wählen Sie dabei Wohnungen, die an Aufzügen oder Luft-</span>
      <span class="ln end">schächten liegen.</span>
    </p>
    <p>
      <span class="ln bullet">In größeren Wohnkomplexen sollten insgesamt mindes-</span>
      <span class="ln">tens 20 % aller Wohnungen in einem Gebäude gemessen</span>
      <span class="ln end">werden.</span>
    </p>
    <p>
      <span class="ln bullet">Es sollten mindestens zwei Wohnräume pro ausgewählte</span>
      <span class="ln">Wohnung gemessen werden. Wählen Sie Räume aus, in</span>
      <span class="ln">denen Sie sich oft aufhalten (z.B. das Wohn- und Schlafzim-</span>
      <span class="ln">mer). Vermeiden Sie aber Räume, in denen das Fenster meh-</span>
      <span class="ln end">rere Stunden am Tag oder in der Nacht geöffnet ist.</span>
    </p>
    <p>
      <span class="ln bullet">Selbst bei einer Einzimmerwohnung sollten Sie zwei</span>
      <span class="ln end">Detektoren aufstellen.</span>
    </p>
  </div>

  <!-- Right column -->
  <svg class="block" style="left:832px;top:63px" width="36" height="53" viewBox="0 0 36 53" aria-hidden="true">
    <rect x="0" y="0" width="36" height="4" fill="var(--red)"/>
    <rect x="0" y="6" width="36" height="47" fill="var(--red)"/>
    <g fill="#fff">
      <rect x="5" y="16" width="6" height="6"/><rect x="15" y="16" width="6" height="6"/><rect x="25" y="16" width="6" height="6"/>
      <rect x="5" y="26" width="6" height="6"/><rect x="15" y="26" width="6" height="6"/><rect x="25" y="26" width="6" height="6"/>
      <rect x="5" y="36" width="6" height="6"/><rect x="15" y="36" width="6" height="6"/><rect x="25" y="36" width="6" height="6"/>
    </g>
  </svg>
  <div class="sub-title" style="left:884px;top:98px">Arbeitsplätze und öffentliche Gebäude</div>

  <div class="block body-text" style="left:832px;top:136px;width:344px">
    <p>
      <span class="ln bullet">Wählen Sie Räume, die regelmäßig mehr als vier Stun-</span>
      <span class="ln end">den pro Tag genutzt werden.</span>
    </p>
    <p>
      <span class="ln bullet">Messen Sie alle unterirdischen Räumlichkeiten, da hier</span>
      <span class="ln">meist das größte Risiko einer erhöhten Radonkonzentrati-</span>
      <span class="ln end">on erwartet wird.</span>
    </p>
    <p>
      <span class="ln bullet">Messen Sie alle Räume im Erdgeschoß. Für größere</span>
      <span class="ln end">Räumlichkeiten empfehlen wir einen Detektor pro 200 m².</span>
    </p>
    <p>
      <span class="ln bullet">In den oberen Etagen sollten Sie mit mindestens zwei</span>
      <span class="ln">Detektoren, sowie mindestens einem Detektor pro 200 m²</span>
      <span class="ln end">messen.</span>
    </p>
    <p>
      <span class="ln bullet">Falls Ihr Arbeitsplatz in einem Radon-Vorsorgegebiet</span>
      <span class="ln">liegt und somit der Messpflicht unterliegt, muss die Mess-</span>
      <span class="ln end">dauer von 12 Monaten eingehalten werden.</span>
    </p>
  </div>

  <svg class="block" style="left:832px;top:399px" width="43" height="33" viewBox="0 0 43 33" aria-hidden="true">
    <g fill="none" stroke="var(--red)" stroke-width="2">
      <rect x="1" y="1" width="41" height="31"/>
      <rect x="5" y="5" width="33" height="23"/>
      <path d="M1 1l4 4M42 1l-4 4M1 32l4-4M42 32l-4-4"/>
      <rect x="10" y="10" width="8" height="6"/>
    </g>
  </svg>
  <div class="sub-title" style="left:884px;top:412px">Platzierung der Detektoren im Raum</div>

  <div class="block body-text" style="left:832px;top:451px;width:344px">
    <p>
      <span class="ln bullet">Platzieren Sie die Detektoren in einem Mindestabstand</span>
      <span class="ln tight">von 20 cm zu Wänden, 50 cm zu Abluftsventilen, sowie 1,50 m</span>
      <span class="ln end">zu Fenstern, Außentüren, Zuluftsventilen und Heizkörpern.</span>
    </p>
    <p>
      <span class="ln bullet">Stellen Sie die Detektoren nicht auf dem Boden, an</span>
      <span class="ln">starken Wärmequellen oder Luftströmen auf. Vermeiden</span>
      <span class="ln">Sie auch Räume mit hoher Luftfeuchtigkeit, wie zum Bei-</span>
      <span class="ln end">spiel das Badezimmer.</span>
    </p>
    <p>
      <span class="ln bullet">Die Detektoren können entweder stehend (auf einem</span>
      <span class="ln">Tisch, im Regal oder einer Schrankwand) oder hängend</span>
      <span class="ln end">mitten im Raum (z.B. von einer Lampe) platziert werden.</span>
    </p>
    <p>
      <span class="ln bullet">Stellen Sie die Detektoren während der gesamten</span>
      <span class="ln end">Messdauer nicht um.</span>
    </p>
    <p>
      <span class="ln bullet">Versuchen Sie nicht das Gehäuse der Detektoren zu</span>
      <span class="ln">öffnen und platzieren Sie diese immer außer Reichweite</span>
      <span class="ln end">von Kindern.</span>
    </p>
  </div>

  <!-- Contact -->
  <div class="contact-bar">
    <svg class="block" style="left:24px;top:20px" width="60" height="54" viewBox="0 0 60 54" aria-hidden="true">
      <path d="M2 2h56v38H37l-7 11-2-11H2z" fill="none" stroke="#fff" stroke-width="2.5" stroke-linejoin="round"/>
      <circle cx="19" cy="21" r="2.2" fill="#fff"/>
      <circle cx="30" cy="21" r="2.2" fill="#fff"/>
      <circle cx="41" cy="21" r="2.2" fill="#fff"/>
    </svg>
    <div class="contact-text">Wenn Sie noch Fragen haben, rufen Sie uns an. Wir sind Ihnen gern behilflich.<br>Telefon +49 (0) 170 555 214 07&nbsp; <span>Mo - Fr / 13 - 15 Uhr</span></div>
  </div>

</div>
</body>
</html>
```